Irrigation Business needs their business cards modernised and revamped

I would like to keep my current logo, colours and revamp the format of the card.

I would like the card to be clean yet important.

Im not sure if you include texture but i would like the named logo to be indented into the card etc.

show me something alive and free something thats clinical to the point yet has a feel of achievement. i would like people to go nice card.

Target Market(s)

high end clients, corporate, sports field manger, the guys that make the decisions

Industry/Entity Type

Business

Contact Information for Business Card

nformation to be included

Dean Harlow (Director)
0487305526
dean@kolvat.biz
www.kestonfieldworks.com

instagram logo
google logo
facebook logo

Colors

Designer to choose colors to be used in the design.

Requirements
Nice to have
• indentations a really nice feel to the card good texture

```html
<!DOCTYPE html>
<html lang="en">
<head>
<meta charset="utf-8">
<title>Keston Fieldworks — Business Cards</title>
<link rel="stylesheet" href="https://fonts.googleapis.com/css2?family=Open+Sans:wght@400;600;700&display=swap">
<style>
  :root {
    --backdrop: #3a3330;
    --card: #111213;
    --card-edge: #1c1d1f;
    --silver: #8d9094;
    --silver-dark: #5e6165;
    --brand-blue: #2f8fd6;
    --brand-green: #3fb36a;
    --text-light: #f2f2f2;
    --rule: #6a6d70;
  }
  * { box-sizing: border-box; margin: 0; padding: 0; }
  html, body {
    width: 1200px; height: 864px; overflow: hidden;
    background: var(--backdrop);
    font-family: "Open Sans", Arial, sans-serif;
  }
  .canvas { position: relative; width: 1200px; height: 864px; }
  .card {
    position: absolute;
    width: 540px; height: 310px;
    background: var(--card);
    border: 1px solid var(--card-edge);
    border-radius: 4px;
    box-shadow: 0 14px 30px rgba(0,0,0,.45);
  }
  /* Front */
  .card-front { left: 80px; top: 80px; display: flex; flex-direction: column; align-items: center; justify-content: center; }
  .front-mark {
    width: 82px; height: 82px; border-radius: 50%;
    background: var(--silver-dark);
    box-shadow: inset 0 2px 4px rgba(0,0,0,.6), 0 1px 0 rgba(255,255,255,.08);
    margin-bottom: 18px;
  }
  .front-name {
    color: var(--silver);
    font-weight: 700; font-size: 30px; letter-spacing: 1px;
    text-transform: uppercase;
  }
  .social-row { display: flex; gap: 8px; margin-top: 22px; }
  .social-dot { width: 18px; height: 18px; border-radius: 50%; background: var(--silver-dark); }
  /* Back */
  .card-back { left: 580px; top: 470px; display: flex; align-items: center; }
  .back-brand { width: 270px; display: flex; flex-direction: column; align-items: center; }
  .back-mark { width: 56px; height: 56px; border-radius: 50%; background: var(--brand-blue); margin-bottom: 10px; }
  .back-name { color: var(--brand-blue); font-weight: 700; font-size: 19px; text-transform: uppercase; letter-spacing: .5px; }
  .divider { width: 1px; height: 120px; background: var(--rule); }
  .contact { padding-left: 26px; }
  .person-name { color: var(--brand-blue); font-weight: 600; font-size: 16px; text-transform: uppercase; }
  .person-role { color: var(--brand-green); font-weight: 600; font-size: 16px; text-transform: uppercase; margin-bottom: 12px; }
  .contact-line { display: flex; align-items: center; gap: 8px; color: var(--text-light); font-size: 14px; line-height: 20px; }
  .contact-line svg { width: 12px; height: 12px; fill: var(--brand-blue); flex: none; }
</style>
</head>
<body>
<main class="canvas">
  <section class="card card-front" aria-label="Card front">
    <div class="front-mark"></div>
    <div class="front-name">Keston Fieldworks</div>
    <div class="social-row">
      <span class="social-dot"></span><span class="social-dot"></span><span class="social-dot"></span>
    </div>
  </section>

  <section class="card card-back" aria-label="Card back">
    <div class="back-brand">
      <div class="back-mark"></div>
      <div class="back-name">Keston Fieldworks</div>
    </div>
    <div class="divider"></div>
    <div class="contact">
      <div class="person-name">Dean Harlow</div>
      <div class="person-role">Director</div>
      <div class="contact-line">
        <svg viewBox="0 0 12 12"><path d="M2 1h3l1 3-1.5 1a6 6 0 0 0 2.5 2.5L8 6l3 1v3a1 1 0 0 1-1 1A9 9 0 0 1 1 2a1 1 0 0 1 1-1z"/></svg>
        0487305526
      </div>
      <div class="contact-line">
        <svg viewBox="0 0 12 12"><path d="M1 2h10v8H1z M1 2l5 4 5-4" stroke="#111213" stroke-width="1"/></svg>
        dean@kolvat.biz
      </div>
      <div class="contact-line">
        <svg viewBox="0 0 12 12"><circle cx="6" cy="6" r="5"/><path d="M1 6h10M6 1v10" stroke="#111213" stroke-width="1"/></svg>
        www.kestonfieldworks.com
      </div>
    </div>
  </section>
</main>
</body>
</html>
```